Wordpress - For IT, Cloud/Hosting, Residential/Commercial Construction Services

We are a holding company for service companies. We want the current Wordpress site modified or a new wordpress site completed. We want this site to be the parent website, that then has pull down menus linking to our other website (currently http://brightwallfix.com, http://q7v.host and would like it to be easy and fluid as we acquire more companies as we have with TKLS, Inc., B&J Construction, Brightwall Fix etc. Model after sites like Pemrose.com, Tallowbine.com, QDV.com,.vanterelm.com

------

The parent is the main site q7v Corp. Below that are sub corps and DBAs. q7v Corp stands for Quick 7 Venture Corp. q7v Offers IT manages services, 24x7 support, Monitoring NOC, Remote Hands, Onsite support services. We have acquired TKLS, Inc, B & J Construction, BrightwallFix.com. We plan to acquire/spin up many companies that offer service, support and installation offerings and will all be known as an q7v Corp Company for branding purposes. We recently had our logo done, but then ran it through 3d glass as we like the look better than the original works. We have original files in vector, but not the 3D galss door render.

Target Market(s)

IT Server and Desktop Support. Construction. Mold Remediation. Mergers and Acquisitions.

Industry/Entity Type

It Company

Coding

Coded - Design and coding required

Font styles to use
Sans Serif

Colors
0792cd

Requirements
Must have
• Clean interface. Modern design. Mobile device and multi browser support. Must be for Wordpress. Job posting with resume submission module.Hook to our Web hosting portal (Tormund) API into VexaLine Reseller portal, customer portal to allow payments to their account etc.. Easy to edit. Easy to add to, Press Release Section, Investor Relations etc.
Should not have
• Slow loading. Played out design. Over use of stock images. Copied from a competitor or something point to such.

```html
<!DOCTYPE html>
<html lang="en">
<head>
<meta charset="utf-8">
<title>q7v Corp</title>
<link href="https://fonts.googleapis.com/css2?family=Montserrat:wght@400;500;600;700&family=Roboto:wght@400;500;700;900&display=swap" rel="stylesheet">
<style>
:root{
  --blue:#0792cd;
  --blue-deep:#0a6fc0;
  --ink:#222;
  --text:#444;
  --grey-btn:#3a3a3a;
  --line:#e3e3e3;
  --white:#fff;
}
*{margin:0;padding:0;box-sizing:border-box}
html,body{width:1200px;height:3197px;overflow:hidden}
body{position:relative;background:var(--white);font-family:"Montserrat",sans-serif;color:var(--text)}
.abs{position:absolute}
a{color:inherit;text-decoration:none}
h1,h2,h3,h4{font-weight:400}

/* header */
.site-header{left:0;top:0;width:1200px;height:94px;background:var(--white);z-index:5}
.brand{left:113px;top:22px;font-family:"Roboto",sans-serif;font-weight:900;font-size:40px;color:var(--blue);letter-spacing:1px}
.main-nav{top:40px;left:0;font-size:15px;color:#333;font-weight:500}
.main-nav a{position:absolute;white-space:nowrap}
.main-nav .active{color:var(--blue)}
.dropdown{left:825px;top:81px;width:228px;height:175px;background:var(--white);border-top:4px solid var(--blue);border-radius:0 0 6px 6px;box-shadow:0 4px 14px rgba(0,0,0,.18);z-index:6;padding:22px 0 0 18px}
.dropdown::before{content:"";position:absolute;left:35px;top:-14px;border:10px solid transparent;border-bottom-color:var(--blue);border-top:0}
.dropdown a{display:flex;align-items:center;gap:12px;font-size:15px;color:#333;height:29px}
.hand{width:16px;height:12px;flex:none}

/* hero */
.hero{left:0;top:94px;width:1200px;height:606px;background:linear-gradient(180deg,#2c8fdc 0%,#1f74c4 45%,#5aa9e3 75%,#eef5fb 100%)}
.hero-title{top:182px;width:1200px;text-align:center;font-family:"Roboto",sans-serif;font-weight:700;font-size:42px;color:var(--white);text-shadow:0 2px 6px rgba(0,0,0,.35)}
.hero-text{top:250px;left:220px;width:760px;text-align:center;font-size:15px;line-height:24px;color:var(--white)}
.btn-outline{left:543px;top:333px;width:112px;height:42px;border:2px solid var(--white);border-radius:22px;color:var(--white);font-size:15px;font-weight:600;display:flex;align-items:center;justify-content:center}
.arrow{top:298px}

/* section headings */
.sec-title{width:1200px;text-align:center;font-family:"Roboto",sans-serif;font-weight:400;font-size:34px;color:var(--blue)}
.sec-title b{font-weight:700}
.rule{left:566px;width:68px;height:3px;background:var(--blue)}

/* about */
.about-text{left:118px;width:964px;text-align:center;font-size:14px;line-height:24px;color:var(--text)}
.btn-solid{left:546px;top:1046px;width:108px;height:43px;border-radius:22px;background:var(--blue);color:var(--white);font-size:15px;font-weight:600;display:flex;align-items:center;justify-content:center}

/* services */
.services-band{left:0;top:1159px;width:1200px;height:322px;background:linear-gradient(120deg,#0b7bd0,#0a67bf)}
.services-title{top:1203px;color:var(--white)}
.service-card{top:1321px;width:294px;height:348px;background:var(--white);border:2px solid #2a2a2a;border-radius:44px;text-align:center;padding:102px 22px 0}
.service-card.featured{border-color:var(--blue-deep)}
.service-card h3{font-family:"Roboto",sans-serif;font-weight:500;font-size:22px;color:var(--ink);margin-bottom:14px}
.service-card.featured h3{color:var(--blue-deep)}
.service-card p{font-size:13.5px;line-height:21px;color:var(--text)}
.service-icon{position:absolute;left:117px;top:22px;width:60px;height:66px}
.toggle{width:64px;height:64px;border-radius:50%;background:var(--grey-btn);top:1632px;display:flex;align-items:center;justify-content:center}
.toggle.featured{background:var(--blue-deep)}
.divider{left:113px;width:976px;height:1px;background:var(--line)}

/* cloud hosting */
.hosting-visual{left:77px;top:1828px;width:388px;height:435px;background:radial-gradient(ellipse at 40% 70%,#3cc3ee 0%,#1aa7de 35%,#e8f2f8 75%,#fff 100%)}
.hosting-title{left:511px;top:1818px;font-family:"Roboto",sans-serif;font-weight:400;font-size:36px;color:var(--blue-deep)}
.hosting-title b{font-weight:700}
.hosting-rule{left:511px;top:1872px;width:78px;height:3px;background:var(--blue)}
.feature{left:511px;width:578px}
.feature svg{position:absolute;left:0;top:0}
.feature h4{margin-left:72px;font-weight:600;font-size:17px;color:var(--ink);margin-bottom:14px}
.feature p{margin-left:72px;font-size:14px;line-height:26px;text-align:justify;color:var(--text)}

/* contact */
.contact-bg{left:0;top:2263px;width:1200px;height:503px;background:linear-gradient(180deg,#0a1826 0%,#0d2236 55%,#173046 75%,#0a1520 100%)}
.contact-title{top:2336px;width:1200px;text-align:center;font-family:"Roboto",sans-serif;font-weight:400;font-size:34px;color:var(--white)}
.contact-title b{font-weight:700}
.contact-text{top:2402px;left:120px;width:960px;text-align:center;font-size:14px;line-height:24px;color:var(--white)}
.field{width:472px;height:45px;border:2px solid #e9e9e9;color:var(--white);font-size:14px;font-weight:600;padding:12px 14px}
.btn-send{left:531px;top:2634px;width:138px;height:45px;border-radius:24px;background:var(--blue-deep);border:2px solid var(--white);color:var(--white);font-weight:700;font-size:15px;display:flex;align-items:center;justify-content:center}

/* footer */
.footer-brand{left:113px;top:2868px;font-family:"Roboto",sans-serif;font-weight:900;font-size:48px;color:var(--blue)}
.footer-about{left:113px;top:2975px;width:366px;font-size:13.5px;line-height:21px;text-align:justify;color:var(--text)}
.footer-head{top:2836px;font-size:22px;font-weight:500;color:var(--blue-deep)}
.footer-head::after{content:"";display:block;width:66px;height:2px;background:var(--blue);margin-top:6px}
.quick-links{left:588px;top:2896px}
.quick-links a{display:flex;align-items:center;gap:12px;font-size:14.5px;color:#333;height:26px}
.contact-item{left:854px;display:flex;gap:16px;align-items:flex-start;font-size:14.5px;line-height:19px;color:#333}
.pin{width:34px;height:34px;border-radius:50%;flex:none}
.footer-rule{left:113px;top:3107px;width:976px;height:1px;background:var(--line)}
.copyright{top:3137px;width:1200px;text-align:center;font-size:14px;font-weight:500;color:#333}
</style>
</head>
<body>

<header class="abs site-header">
  <a class="abs brand" href="#">q7v Corp</a>
  <nav class="abs main-nav">
    <a style="left:503px" href="#">HOME</a>
    <a style="left:580px" href="#">ABOUT US</a>
    <a style="left:684px" href="#">OUR SERVICES</a>
    <a class="active" style="left:818px" href="#">COMPANY</a>
    <a style="left:925px" href="#">BLOG</a>
    <a style="left:995px" href="#">CONTACT US</a>
  </nav>
</header>
<div class="abs dropdown">
  <a href="#"><svg class="hand" viewBox="0 0 16 12"><path d="M1 5h9l-3-3M1 5v5h9l2-5" fill="none" stroke="#0792cd" stroke-width="1.6" stroke-linecap="round" stroke-linejoin="round"/></svg>q7v.host</a>
  <a href="#"><svg class="hand" viewBox="0 0 16 12"><path d="M1 5h9l-3-3M1 5v5h9l2-5" fill="none" stroke="#0792cd" stroke-width="1.6" stroke-linecap="round" stroke-linejoin="round"/></svg>Brightwallfix</a>
  <a href="#"><svg class="hand" viewBox="0 0 16 12"><path d="M1 5h9l-3-3M1 5v5h9l2-5" fill="none" stroke="#0792cd" stroke-width="1.6" stroke-linecap="round" stroke-linejoin="round"/></svg>TKLS, Inc</a>
  <a href="#"><svg class="hand" viewBox="0 0 16 12"><path d="M1 5h9l-3-3M1 5v5h9l2-5" fill="none" stroke="#0792cd" stroke-width="1.6" stroke-linecap="round" stroke-linejoin="round"/></svg>B&amp;J Construction</a>
</div>

<section class="abs hero" role="img" aria-label="Hand holding a glowing cloud security network above a white cloud border and a laptop showing a network diagram"></section>
<h1 class="abs hero-title">q7v CORP</h1>
<p class="abs hero-text">Nemo enim ipsam voluptatem quia voluptas sit aspernatur aut odit aut fugit, sed quia consequuntur magni dolores eos qui ratione voluptatem sequi nesciunt.</p>
<a class="abs btn-outline" href="#">Read More</a>
<svg class="abs arrow" style="left:38px" width="24" height="44" viewBox="0 0 24 44"><path d="M20 2L4 22l16 20" fill="none" stroke="#fff" stroke-width="2.5"/></svg>
<svg class="abs arrow" style="left:1140px" width="24" height="44" viewBox="0 0 24 44"><path d="M4 2l16 20L4 42" fill="none" stroke="#fff" stroke-width="2.5"/></svg>

<h2 class="abs sec-title" style="top:768px">About <b>q7v Corp</b></h2>
<div class="abs rule" style="top:830px"></div>
<p class="abs about-text" style="top:870px">Nemo enim ipsam voluptatem quia voluptas sit aspernatur aut odit aut fugit, sed quia consequuntur magni dolores eos qui ratione voluptatem sequi nesciunt. Neque porro quisquam est, qui dolorem ipsum quia dolor sit amet, consectetur, adipisci velit, sed quia non numquam eius modi tempora incidunt ut labore et dolore magnam aliquam quaerat voluptatem.</p>
<p class="abs about-text" style="top:964px">Sed ut perspiciatis unde omnis iste natus error sit voluptatem accusantium doloremque laudantium, totam rem aperiam, eaque ipsa quae ab illo inventore veritatis et quasi architecto beatae vitae dicta sunt explicabo.</p>
<a class="abs btn-solid" href="#">Read More</a>

<section class="abs services-band"></section>
<h2 class="abs sec-title services-title" style="color:#fff">Our <b>Services</b></h2>
<div class="abs rule" style="top:1264px;background:#fff"></div>

<article class="abs service-card" style="left:115px">
  <svg class="service-icon" viewBox="0 0 60 66"><g fill="none" stroke="#333" stroke-width="2.5"><rect x="6" y="8" width="48" height="34" rx="2"/><path d="M2 48h56l-4 6H6z"/><circle cx="30" cy="25" r="11"/><path d="M19 25h22M30 14c-5 6-5 16 0 22M30 14c5 6 5 16 0 22"/></g></svg>
  <h3>Services In IT</h3>
  <p>Sed ut perspiciatis unde omnis iste natus error sit voluptatem accusantium dolore mque laudantium, totam rem aperiam, eaque ipsa quae ab illo inventore veritatis et quasi architecto beatae vitae dicta sunt explicabo.</p>
</article>
<article class="abs service-card featured" style="left:452px">
  <svg class="service-icon" viewBox="0 0 60 66"><g fill="none" stroke="#0a6fc0" stroke-width="2.5"><path d="M14 36a10 10 0 0 1 2-20 14 14 0 0 1 27-2 10 10 0 0 1 3 22z"/><ellipse cx="30" cy="26" rx="9" ry="3"/><path d="M21 26v12c0 4 18 4 18 0V26M30 42v10M18 58h24M30 52v6"/></g></svg>
  <h3>Commercial Services</h3>
  <p>Sed ut perspiciatis unde omnis iste natus error sit voluptatem accusantium dolore mque laudantium, totam rem aperiam, eaque ipsa quae ab illo inventore veritatis et quasi architecto beatae vitae dicta sunt explicabo.</p>
</article>
<article class="abs service-card" style="left:791px">
  <svg class="service-icon" viewBox="0 0 60 66"><g fill="none" stroke="#333" stroke-width="2.5"><path d="M30 4v10M24 14h12l-2 8H26z"/><path d="M8 30h44v28H8z"/><path d="M8 30l22-8 22 8M16 38v14M24 38v14M32 38v14M40 38v14"/></g></svg>
  <h3>Construction Services</h3>
  <p>Sed ut perspiciatis unde omnis iste natus error sit voluptatem accusantium dolore mque laudantium, totam rem aperiam, eaque ipsa quae ab illo inventore veritatis et quasi architecto beatae vitae dicta sunt explicabo.</p>
</article>
<div class="abs toggle" style="left:230px"><svg width="26" height="26" viewBox="0 0 26 26"><circle cx="13" cy="13" r="12" fill="#fff"/><path d="M7 10l6 6 6-6" fill="none" stroke="#3a3a3a" stroke-width="3"/></svg></div>
<div class="abs toggle featured" style="left:567px"><svg width="26" height="26" viewBox="0 0 26 26"><circle cx="13" cy="13" r="12" fill="#fff"/><path d="M7 10l6 6 6-6" fill="none" stroke="#0a6fc0" stroke-width="3"/></svg></div>
<div class="abs toggle" style="left:906px"><svg width="26" height="26" viewBox="0 0 26 26"><circle cx="13" cy="13" r="12" fill="#fff"/><path d="M7 10l6 6 6-6" fill="none" stroke="#3a3a3a" stroke-width="3"/></svg></div>

<div class="abs divider" style="top:1762px"></div>

<div class="abs hosting-visual" role="img" aria-label="Businessman in a suit holding blue cloud shapes"></div>
<h2 class="abs hosting-title">Cloud/<b>Hosting</b></h2>
<div class="abs hosting-rule"></div>

<div class="abs feature" style="top:1904px">
  <svg width="46" height="46" viewBox="0 0 46 46"><g fill="none" stroke="#0a6fc0" stroke-width="2"><rect x="6" y="4" width="26" height="32"/><path d="M12 12h14M12 18h14M12 24h10"/><rect x="2" y="34" width="42" height="8"/></g></svg>
  <h4>Nemo enim voluptatem</h4>
  <p>Nemo enim ipsam voluptatem quia voluptas sit aspernatur aut odit aut fugit, sed quia consequuntur magni eos qui ratione voluptatem.</p>
</div>
<div class="abs feature" style="top:2008px">
  <svg width="46" height="46" viewBox="0 0 46 46"><g fill="none" stroke="#0a6fc0" stroke-width="2.2"><rect x="4" y="6" width="38" height="26" rx="2"/><path d="M16 40h14M23 32v8"/></g></svg>
  <h4>Cloud Services</h4>
  <p>Nemo enim ipsam voluptatem quia voluptas sit aspernatur aut odit aut fugit, sed quia consequuntur magni eos qui ratione voluptatem.</p>
</div>
<div class="abs feature" style="top:2110px">
  <svg width="50" height="46" viewBox="0 0 50 46"><g fill="#0a6fc0"><circle cx="14" cy="16" r="7"/><path d="M2 42c0-10 6-15 12-15s12 5 12 15z"/></g><g fill="none" stroke="#0a6fc0" stroke-width="2"><rect x="26" y="4" width="22" height="14" rx="2"/><path d="M30 18l-2 5 6-5"/></g></svg>
  <h4>Sed ut perspiciatis</h4>
  <p>Nemo enim ipsam voluptatem quia voluptas sit aspernatur aut odit aut fugit, sed quia consequuntur magni eos qui ratione voluptatem.</p>
</div>

<section class="abs contact-bg" role="img" aria-label="Dark background of glowing financial market data"></section>
<h2 class="abs contact-title">Contact <b>Form</b></h2>
<p class="abs contact-text">Nemo enim ipsam voluptatem quia voluptas sit aspernatur aut odit aut fugit, sed quia consequuntur magni dolores eos qui ratione voluptatem sequi nesciunt.</p>
<div class="abs field" style="left:119px;top:2497px">First Name</div>
<div class="abs field" style="left:608px;top:2497px">Phone</div>
<div class="abs field" style="left:119px;top:2557px">United Arab Emirates</div>
<div class="abs field" style="left:608px;top:2557px">Email</div>
<a class="abs btn-send" href="#">SEND NOW</a>

<div class="abs footer-brand">q7v Corp</div>
<p class="abs footer-about">Sed ut perspiciatis unde omnis iste natus error sit vo luptatem accusantium doloremque laudantium, totam rem aperiam, eaque ipsa.</p>

<h3 class="abs footer-head" style="left:588px">Quick Links</h3>
<nav class="abs quick-links">
  <a href="#"><svg class="hand" viewBox="0 0 16 12"><path d="M1 5h9l-3-3M1 5v5h9l2-5" fill="none" stroke="#0792cd" stroke-width="1.6" stroke-linecap="round" stroke-linejoin="round"/></svg>Home</a>
  <a href="#"><svg class="hand" viewBox="0 0 16 12"><path d="M1 5h9l-3-3M1 5v5h9l2-5" fill="none" stroke="#0792cd" stroke-width="1.6" stroke-linecap="round" stroke-linejoin="round"/></svg>About Us</a>
  <a href="#"><svg class="hand" viewBox="0 0 16 12"><path d="M1 5h9l-3-3M1 5v5h9l2-5" fill="none" stroke="#0792cd" stroke-width="1.6" stroke-linecap="round" stroke-linejoin="round"/></svg>Our Services</a>
  <a href="#"><svg class="hand" viewBox="0 0 16 12"><path d="M1 5h9l-3-3M1 5v5h9l2-5" fill="none" stroke="#0792cd" stroke-width="1.6" stroke-linecap="round" stroke-linejoin="round"/></svg>Company</a>
  <a href="#"><svg class="hand" viewBox="0 0 16 12"><path d="M1 5h9l-3-3M1 5v5h9l2-5" fill="none" stroke="#0792cd" stroke-width="1.6" stroke-linecap="round" stroke-linejoin="round"/></svg>Blog</a>
  <a href="#"><svg class="hand" viewBox="0 0 16 12"><path d="M1 5h9l-3-3M1 5v5h9l2-5" fill="none" stroke="#0792cd" stroke-width="1.6" stroke-linecap="round" stroke-linejoin="round"/></svg>Contact</a>
</nav>

<h3 class="abs footer-head" style="left:854px">Contact Us</h3>
<div class="abs contact-item" style="top:2890px">
  <svg class="pin" viewBox="0 0 34 34"><circle cx="17" cy="17" r="16" fill="none" stroke="#0792cd" stroke-width="1.5"/><path d="M17 9a5 5 0 0 1 5 5c0 4-5 10-5 10s-5-6-5-10a5 5 0 0 1 5-5z" fill="#0792cd"/><circle cx="17" cy="14" r="2" fill="#fff"/></svg>
  <span>q7v Corp,<br>123, Marlowe Street,<br>Port-Aldin, UK.</span>
</div>
<div class="abs contact-item" style="top:2978px;align-items:center">
  <svg class="pin" viewBox="0 0 34 34"><circle cx="17" cy="17" r="16" fill="none" stroke="#0792cd" stroke-width="1.5"/><path d="M11 10l4-1 2 4-2 2a10 10 0 0 0 4 4l2-2 4 2-1 4c-7 0-13-6-13-13z" fill="#0792cd"/></svg>
  <span>Phone: +180 025 4471</span>
</div>
<div class="abs contact-item" style="top:3028px;align-items:center">
  <svg class="pin" viewBox="0 0 34 34"><circle cx="17" cy="17" r="16" fill="#0792cd"/><rect x="9" y="11" width="16" height="12" rx="1" fill="#fff"/><path d="M9 12l8 6 8-6" fill="none" stroke="#0792cd" stroke-width="1.5"/></svg>
  <span>Mail: info@q7vcorp.com</span>
</div>

<div class="abs footer-rule"></div>
<p class="abs copyright">Copyrights @ 2018 q7v Corp. All Rights Reserved.</p>

</body>
</html>
```